The Grind Show With Marcus Pellow

I am looking for a 1 page static HTML website that is mobile friendly that will become the landing page to my podcast which is already established. The 1 page website should comprise of a strong visual branding inline with the current branding of the podcast (see images and links below) for and contain the following elements / functions:

1. About the podcast section
2. Links to the podcast on all major platforms
3. About the host section
4. Awards
5. Links to:
- Guest Booking - to go to email
- Sponsorship Enquiry - to go to email
- Media Enquiries
- Book Podcast Recording

Here are the relevant links:
https://www.vbq.co.za/podcasts/grind-marcus-pellow/
you can find the platform links there

Velora FM link: https://velora.fm/c/4219

Sponsor enquiries: https://www.adquill.co.za/
Media and guest enquiries go to linette@marcuspellow.co.za

Details for bookwise link for booking recording

<!-- Bookwise link widget begin -->
<link href="https://assets.bookwise.com/assets/external/widget.css" rel="stylesheet">
<script src="https://assets.bookwise.com/assets/external/widget.js" type="text/javascript" async></script>
<a href="" onclick="Bookwise.initPopupWidget({url: 'https://bookwise.com/coinclan47/podcast'});return false;">Schedule time with me</a>
<!-- Bookwise link widget end -->

Target Market(s)

Podcast Listeners men and woman age 21-60

Industry/Entity Type

Podcasting and Media

Coding

Coded - Design and coding required

Number of Pages Required

1 page

Font styles to use
Sans Serif

Requirements
Must have
• Mobile friendly

```html
<!DOCTYPE html>
<html lang="en">
<head>
<meta charset="utf-8">
<meta name="viewport" content="width=device-width, initial-scale=1">
<title>The Grind Show With Marcus Pellow</title>
<link rel="stylesheet" href="https://fonts.googleapis.com/css2?family=Oswald:wght@500;600;700&family=Open+Sans:wght@400;600&display=swap">
<style>
:root{
  --ink:#141312;
  --ink-soft:#1d1b18;
  --gold:#d6a92c;
  --gold-deep:#b98d1c;
  --gold-light:#e7bf45;
  --white:#ffffff;
  --text:#2b2b2b;
  --muted:#e6e6e6;
  --dots:#d2d2d2;
}
*{box-sizing:border-box;margin:0;padding:0}
html,body{width:1200px;height:3671px;overflow:hidden}
body{font-family:"Open Sans",Arial,sans-serif;color:var(--text);background:var(--white);position:relative}
.display{font-family:"Oswald","Arial Narrow",sans-serif;font-weight:700;text-transform:uppercase;letter-spacing:-0.5px}
.abs{position:absolute}

/* hero */
.hero{position:absolute;left:0;top:0;width:1200px;height:513px;
  background:radial-gradient(ellipse 420px 300px at 830px 290px,rgba(214,169,44,.45),rgba(214,169,44,0) 70%),var(--ink);overflow:hidden}
.nav a{position:absolute;top:48px;color:var(--white);font-size:14px;text-decoration:none;text-transform:uppercase}
.nav a.active{color:var(--gold);text-decoration:underline}
.brand{position:absolute;left:540px;top:26px;width:120px;text-align:center;color:var(--white);line-height:1}
.brand .small{font-size:13px;font-family:"Oswald",sans-serif;font-weight:600}
.brand .big{font-size:38px;font-family:"Oswald",sans-serif;font-weight:700}
.hero-title{position:absolute;left:125px;top:192px;font-size:78px;line-height:84px;color:var(--white);text-shadow:4px 4px 0 var(--gold-deep)}
.rocket{position:absolute;left:734px;top:107px;width:406px;height:270px;border-radius:20px;
  background:radial-gradient(ellipse at 50% 50%,rgba(231,191,69,.35),rgba(20,19,18,0) 70%)}

/* cta cards */
.cta{position:absolute;top:550px;width:238px;height:140px;border-radius:6px;
  background:linear-gradient(135deg,var(--gold-light),var(--gold-deep));color:var(--white);
  box-shadow:0 8px 14px rgba(0,0,0,.18);text-decoration:none}
.cta span{position:absolute;left:22px;top:34px;font-size:31px;line-height:35px}
.cta svg{position:absolute;left:180px;top:72px}

/* about */
.photo{border-radius:14px;background:radial-gradient(ellipse at 50% 35%,#6a5222,#1a1611 70%)}
.dots{background-image:radial-gradient(circle,var(--dots) 2px,transparent 2.5px);background-size:20px 20px}
.section-title{font-size:68px;color:var(--ink);text-shadow:3px 3px 0 var(--gold)}
.about-sub{left:624px;top:894px;font-size:17px;font-weight:600;color:#111}
.about-text{left:624px;top:930px;width:466px;font-size:15px;line-height:28.3px;color:#333}

/* episodes */
.listen{left:0;width:1200px;top:1322px;text-align:center;font-size:18px;color:#222}
.episode{position:absolute;width:461px;height:103px;border:1px solid var(--muted);background:var(--white)}
.episode .thumb{position:absolute;left:0;top:0;width:101px;height:101px;background:linear-gradient(160deg,#4a3a1c,#121110)}
.episode .title{position:absolute;left:124px;top:20px;width:230px;font-size:15.5px;line-height:22px;color:#222}
.episode .date{position:absolute;left:124px;font-size:11.5px;color:#333}
.episode svg{position:absolute;left:410px;top:40px}
.btn{position:absolute;left:523px;top:1667px;width:154px;height:62px;border-radius:3px;background:var(--gold);
  color:var(--white);font-size:21px;line-height:62px;text-align:center;text-decoration:none}

/* dark bands */
.band{position:absolute;left:0;width:1200px;background:radial-gradient(ellipse 520px 260px at 600px 100%,rgba(214,169,44,.45),rgba(214,169,44,0) 70%),var(--ink)}
.band-title{position:absolute;left:0;width:1200px;text-align:center;font-size:68px;color:var(--white);text-shadow:3px 3px 0 var(--gold-deep)}
.platform{position:absolute;top:1968px;width:225px;height:97px;border-radius:4px;background:var(--white);
  display:flex;align-items:center;justify-content:center;gap:10px;font-size:20px;color:#222;text-decoration:none;font-weight:600}
.platform i{display:block;width:28px;height:28px;border-radius:50%;background:var(--gold)}

/* host */
.host-text{left:111px;top:2386px;width:402px;font-size:15px;line-height:28.3px;color:#333}
.host-text p+p{margin-top:10px}

/* awards */
.award{position:absolute;top:2953px;width:465px;height:464px;border-radius:4px}
.rule{left:111px;top:3488px;width:976px;height:1px;background:#3a3835}
.footer-brand{left:540px;top:3524px;width:120px;text-align:center;color:var(--white);line-height:1}
.copy{left:0;width:1200px;top:3615px;text-align:center;font-size:15px;color:var(--white)}
</style>
</head>
<body>

<header class="hero">
  <nav class="nav">
    <a href="#about" style="left:115px">About</a>
    <a href="#platforms" style="left:195px">Platforms</a>
    <a href="#host" style="left:309px">The Host</a>
    <a href="#awards" style="left:408px">Awards</a>
    <a href="mailto:linette@marcuspellow.co.za" style="left:757px">Guest</a>
    <a href="https://bookwise.com/coinclan47/podcast" style="left:832px">Podcast Recording</a>
    <a class="active" href="mailto:linette@marcuspellow.co.za" style="left:1025px">Enquiry</a>
  </nav>
  <div class="brand"><div class="small">THE</div><div class="big">GRIND</div></div>
  <h1 class="hero-title display">The Real Grind<br>Has No Limits</h1>
  <div class="rocket" role="img" aria-label="Line illustration of a gold rocket launching among stars and clouds"></div>
</header>

<a class="cta display" href="mailto:linette@marcuspellow.co.za" style="left:111px"><span>Guest<br>Booking</span>
  <svg width="28" height="20" viewBox="0 0 28 20"><path d="M1 10h24M17 2l8 8-8 8" fill="none" stroke="#fff" stroke-width="2.4"/></svg></a>
<a class="cta display" href="https://www.adquill.co.za/" style="left:358px"><span>Sponsorship<br>Enquiry</span>
  <svg width="28" height="20" viewBox="0 0 28 20"><path d="M1 10h24M17 2l8 8-8 8" fill="none" stroke="#fff" stroke-width="2.4"/></svg></a>
<a class="cta display" href="mailto:linette@marcuspellow.co.za" style="left:604px"><span>Media<br>Enquiries</span>
  <svg width="28" height="20" viewBox="0 0 28 20"><path d="M1 10h24M17 2l8 8-8 8" fill="none" stroke="#fff" stroke-width="2.4"/></svg></a>
<a class="cta display" href="https://bookwise.com/coinclan47/podcast" style="left:849px"><span>Book Podcast<br>Recording</span>
  <svg width="28" height="20" viewBox="0 0 28 20"><path d="M1 10h24M17 2l8 8-8 8" fill="none" stroke="#fff" stroke-width="2.4"/></svg></a>

<section id="about">
  <div class="abs dots" style="left:495px;top:765px;width:66px;height:472px"></div>
  <div class="abs photo" style="left:111px;top:765px;width:391px;height:472px" role="img" aria-label="Podcast cover art: the host in a dark suit, arms crossed, above the show title"></div>
  <h2 class="abs section-title display" style="left:624px;top:780px">About Podcast</h2>
  <p class="abs about-sub">The Grind with Marcus Pellow</p>
  <p class="abs about-text">Money, motivation, and inspiration wrapped up in a brutally honest and direct podcast from a man who's walked the walk and is now talking the talk. The Grind with Marcus Pellow is the collective experience of a man who went from homeless to building his business empire on pure grit and determination. Marcus takes your questions and answers them with total honesty, no frills, no beating around the bush. From money to career to business, no subject is off-limits, because the real grind has no limits.</p>

  <p class="abs listen">LISTEN HERE</p>

  <div class="episode" style="left:128px;top:1382px"><div class="thumb" role="img" aria-label="Episode cover art"></div>
    <p class="title">Where to start in marketing a business</p><p class="date" style="top:70px">12 DEC 9AM</p>
    <svg width="20" height="24" viewBox="0 0 20 24"><path d="M2 1l17 11L2 23z" fill="var(--gold)"/></svg></div>
  <div class="episode" style="left:611px;top:1382px"><div class="thumb" role="img" aria-label="Episode cover art"></div>
    <p class="title">How to start your side grind</p><p class="date" style="top:54px">05 DEC 9AM</p>
    <svg width="20" height="24" viewBox="0 0 20 24"><path d="M2 1l17 11L2 23z" fill="var(--gold)"/></svg></div>
  <div class="episode" style="left:128px;top:1498px"><div class="thumb" role="img" aria-label="Episode cover art"></div>
    <p class="title">When to take on staff in your business</p><p class="date" style="top:70px">28 NOV 5AM</p>
    <svg width="20" height="24" viewBox="0 0 20 24"><path d="M2 1l17 11L2 23z" fill="var(--gold)"/></svg></div>
  <div class="episode" style="left:611px;top:1498px"><div class="thumb" role="img" aria-label="Episode cover art"></div>
    <p class="title">Marriage and business-can it work?</p><p class="date" style="top:70px">21 NOV 7AM</p>
    <svg width="20" height="24" viewBox="0 0 20 24"><path d="M2 1l17 11L2 23z" fill="var(--gold)"/></svg></div>

  <a class="btn display" href="https://www.vbq.co.za/podcasts/grind-marcus-pellow/">View All</a>
</section>

<section id="platforms" class="band" style="top:1784px;height:348px">
  <h2 class="band-title display" style="top:48px">Major Platforms</h2>
</section>
<a class="platform" href="https://www.vbq.co.za/podcasts/grind-marcus-pellow/" style="left:111px"><i></i>Orchard Podcasts</a>
<a class="platform" href="https://www.vbq.co.za/podcasts/grind-marcus-pellow/" style="left:362px"><i></i>Lumen Podcasts</a>
<a class="platform" href="https://www.vbq.co.za/podcasts/grind-marcus-pellow/" style="left:611px"><i></i>Soundwell</a>
<a class="platform" href="https://velora.fm/c/4219" style="left:862px">Velora FM</a>

<section id="host">
  <h2 class="abs section-title display" style="left:111px;top:2268px">The Host</h2>
  <div class="abs host-text">
    <p>Lorem ipsum dolor sit amet, consectetur adipiscing elit, sed do eiusmod tempor incididunt ut labore et dolore magna aliqua. Ut enim ad minim veniam, quis nostrud exercitation ullamco laboris nisi ut aliquip ex ea com modo consequat. Duis aute irure dolor in reprehender it in voluptate velit esse cillum dolore eu fugiat.</p>
    <p>Ut enim ad minim veniam, quis nostrud exercitation ullamco laboris nisi ut aliquip ex ea com modo conse quat. Duis aute irure dolor in reprehender.</p>
  </div>
  <div class="abs dots" style="left:630px;top:2230px;width:66px;height:472px"></div>
  <div class="abs photo" style="left:698px;top:2230px;width:391px;height:472px;background:linear-gradient(180deg,#2a2623,#0f0e0d)" role="img" aria-label="The host smiling, holding open a black tuxedo jacket over a show-branded shirt"></div>
</section>

<section id="awards" class="band" style="top:2782px;height:889px;background:radial-gradient(ellipse 520px 220px at 600px 0,rgba(214,169,44,.4),rgba(214,169,44,0) 70%),var(--ink)">
  <h2 class="band-title display" style="top:50px">Awards</h2>
</section>
<div class="award" style="left:118px;background:linear-gradient(160deg,#3c2a86,#1f1558)" role="img" aria-label="Kestrel Awards, Voices of the Future: The Grind, finance category finalist"></div>
<div class="award" style="left:617px;background:linear-gradient(160deg,#3c7fc4,#6b3fa6)" role="img" aria-label="Streamline Creator Awards: Podcast of the Year nominee, The Grind with Marcus Pellow"></div>

<footer>
  <div class="abs rule"></div>
  <div class="abs footer-brand"><div class="small" style="font-family:Oswald,sans-serif;font-weight:600;font-size:13px">THE</div><div style="font-family:Oswald,sans-serif;font-weight:700;font-size:38px">GRIND</div></div>
  <p class="abs copy">2024 The Grind with Marcus Pellow. All Rights Reserved.</p>
</footer>

</body>
</html>
```